FunBrixo Business Card

We need a business card design for our company. We sell construction-themed amusement rides for kids.

Contact Information for Business Card

Contact info on business card should include:
Carl Dunning
Co-Founder & COO
(833) 571-FUNBRIX
Carl@funbrixo-demo.com
www.funbrixo-demo.com

```html
<!DOCTYPE html>
<html lang="en">
<head>
<meta charset="utf-8">
<title>FunBrixo Business Card</title>
<link href="https://fonts.googleapis.com/css2?family=Arimo:wght@400;700&display=swap" rel="stylesheet">
<style>
  :root {
    --backdrop: #2e2e30;
    --card: #7b7b7d;
    --orange: #f26b21;
    --text: #f2f2f2;
    --rule: #d9d9d9;
    --blue: #1ba9e1;
    --magenta: #e5177e;
    --amber: #f7a21b;
    --helmet: #f3c83a;
    --vest: #e4572e;
    --denim: #2f4e8a;
  }
  * { margin: 0; padding: 0; box-sizing: border-box; }
  html, body { width: 1200px; height: 866px; overflow: hidden; }
  body {
    background: var(--backdrop);
    font-family: "Arimo", Arial, sans-serif;
    display: flex;
    flex-direction: column;
    align-items: center;
    justify-content: center;
    gap: 40px;
  }
  .card {
    position: relative;
    width: 680px;
    height: 388px;
    background: var(--card);
    box-shadow: 0 6px 18px rgba(0,0,0,.45);
    overflow: hidden;
  }
  .card--front .crew-illustration {
    position: absolute;
    left: 20px;
    bottom: 0;
    width: 300px;
    height: 340px;
    background: linear-gradient(160deg, var(--helmet) 0%, var(--vest) 45%, #e9e9e9 70%, var(--denim) 100%);
    border-radius: 120px 120px 0 0;
    opacity: .85;
  }
  .contact {
    position: absolute;
    left: 350px;
    top: 110px;
    width: 300px;
    color: var(--text);
  }
  .contact__name {
    color: var(--orange);
    font-size: 26px;
    font-weight: 400;
    letter-spacing: 1px;
    text-transform: uppercase;
  }
  .contact__title { font-size: 19px; margin-top: 2px; }
  .contact__divider {
    display: flex;
    align-items: center;
    gap: 8px;
    margin: 12px 0 10px;
  }
  .contact__divider::before,
  .contact__divider::after {
    content: "";
    flex: 1;
    height: 1px;
    background: var(--rule);
  }
  .icon {
    width: 30px; height: 26px;
    display: flex; align-items: center; justify-content: center;
    border-radius: 3px;
  }
  .icon--phone { background: var(--blue); }
  .icon--mail { background: var(--magenta); }
  .icon--web { background: var(--amber); }
  .contact__line { font-size: 17px; line-height: 1.35; letter-spacing: .3px; }
  .card--back { display: flex; align-items: center; justify-content: center; }
  .brand-name {
    color: var(--orange);
    font-size: 78px;
    font-weight: 700;
    letter-spacing: 1px;
    display: flex;
    align-items: center;
    gap: 18px;
  }
  .brand-name__dot {
    width: 26px; height: 26px;
    border-radius: 50%;
    background: var(--orange);
  }
</style>
</head>
<body>
  <section class="card card--front">
    <div class="crew-illustration" role="img" aria-label="Cartoon illustration of two construction workers in yellow hard hats and safety vests"></div>
    <div class="contact">
      <h1 class="contact__name">Carl Dunning</h1>
      <p class="contact__title">Co-Founder &amp; COO</p>
      <div class="contact__divider">
        <span class="icon icon--phone">
          <svg width="16" height="16" viewBox="0 0 24 24"><path d="M6.6 10.8a15 15 0 0 0 6.6 6.6l2.2-2.2a1 1 0 0 1 1-.25 11.4 11.4 0 0 0 3.6.57 1 1 0 0 1 1 1V20a1 1 0 0 1-1 1A17 17 0 0 1 3 4a1 1 0 0 1 1-1h3.5a1 1 0 0 1 1 1c0 1.25.2 2.45.57 3.57a1 1 0 0 1-.25 1z" fill="#1e1e1e"/></svg>
        </span>
        <span class="icon icon--mail">
          <svg width="18" height="14" viewBox="0 0 18 14"><rect x="1" y="1" width="16" height="12" fill="#1e1e1e"/><path d="M1 1l8 7 8-7" stroke="#e5177e" stroke-width="1.5" fill="none"/></svg>
        </span>
        <span class="icon icon--web">
          <svg width="16" height="16" viewBox="0 0 16 16"><circle cx="8" cy="8" r="7" fill="#1e1e1e"/><ellipse cx="8" cy="8" rx="3" ry="7" stroke="#f7a21b" fill="none"/><path d="M1 8h14" stroke="#f7a21b"/></svg>
        </span>
      </div>
      <p class="contact__line">(833) 571-FUNBRIX</p>
      <p class="contact__line">Carl@funbrixo-demo.com</p>
      <p class="contact__line">www.funbrixo-demo.com</p>
    </div>
  </section>

  <section class="card card--back">
    <div class="brand-name">
      <span>FunBrixo</span>
      <span class="brand-name__dot"></span>
    </div>
  </section>
</body>
</html>
```